Engagement party email invitation

I need an invitation designed for my upcoming engagement party. I would like the attached picture to be encircled by gum leaves or some sort of garland of green leaves.

Traditional text typeface eg Sackers Gothic Light or Mrs Eaves.

Thanks
Marnie

Font styles to use
Serif
Script

```html
<!DOCTYPE html>
<html lang="en">
<head>
<meta charset="utf-8">
<title>Engagement Invitation – Marnie &amp; Daniel</title>
<link rel="stylesheet" href="https://fonts.googleapis.com/css2?family=Cormorant+Garamond:wght@600;700&family=Libre+Caslon+Text:wght@700&display=swap">
<style>
  :root {
    --sky: #f2fbfb;
    --mist: #e2f3f3;
    --skyline: #cfe8ef;
    --hill-green: #b4d3bd;
    --hill-shade: #a6c3c4;
    --harbour: #b3e6ea;
    --harbour-deep: #9fdbe2;
    --roof-lilac: #cbbfdc;
    --band: rgba(255, 255, 255, 0.6);
    --gold-light: #f0c566;
    --gold: #b87a14;
    --gold-dark: #5e3604;
    --amp-pale: #f6f7b0;
    --amp-mid: #d8de70;
    --ink-shadow: rgba(40, 22, 0, 0.6);
  }
  * { margin: 0; padding: 0; box-sizing: border-box; }
  html, body {
    width: 1200px; height: 628px; overflow: hidden; background: #ffffff;
  }
  .invitation {
    position: relative; width: 1200px; height: 628px; overflow: hidden;
  }
  .harbour-scene {
    position: absolute; inset: 0;
    background: linear-gradient(172deg,
      var(--sky) 0%,
      var(--mist) 22%,
      var(--skyline) 34%,
      var(--hill-green) 46%,
      var(--hill-shade) 56%,
      var(--harbour) 66%,
      var(--harbour-deep) 82%,
      var(--harbour) 90%,
      var(--roof-lilac) 100%);
  }
  .info-band {
    position: absolute; left: 0; right: 0; top: 414px; height: 138px;
    background: var(--band);
  }
  .gilt {
    background: linear-gradient(180deg, var(--gold-light) 0%, var(--gold) 50%, var(--gold-dark) 100%);
    -webkit-background-clip: text; background-clip: text;
    color: transparent;
    filter: drop-shadow(1px 2px 1px var(--ink-shadow));
  }
  .line {
    position: absolute; left: 0; right: 0; text-align: center; white-space: nowrap;
    font-family: "Cormorant Garamond", Georgia, serif; font-weight: 700;
    font-variant-numeric: oldstyle-nums;
    line-height: 1;
  }
  .hosts { top: 56px; font-size: 64px; letter-spacing: 3.5px; }
  .invite-line { top: 136px; font-size: 62px; letter-spacing: 2.5px; }
  .couple {
    top: 244px; font-family: "Libre Caslon Text", Georgia, serif;
    font-size: 116px; letter-spacing: 1px;
  }
  .couple .amp {
    background: linear-gradient(180deg, var(--amp-pale) 0%, var(--amp-mid) 100%);
    -webkit-background-clip: text; background-clip: text;
  }
  .date { top: 424px; font-size: 58px; font-weight: 600; letter-spacing: 3px; }
  .venue { top: 494px; font-size: 58px; font-weight: 600; letter-spacing: 3px; }
</style>
</head>
<body>
<main class="invitation">
  <div class="harbour-scene" role="img" aria-label="Soft watercolour view of a leafy harbour suburb with a city skyline, moored boats and jetties"></div>
  <div class="info-band"></div>

  <p class="line hosts gilt">Helen &amp; Robert Tanner</p>
  <p class="line invite-line gilt">invite you to celebrate the engagement of</p>
  <h1 class="line couple gilt">Marnie <span class="amp">&amp;</span> Daniel</h1>
  <p class="line date gilt">Saturday 23 January 2021, 6.30pm</p>
  <p class="line venue gilt">17 Bay Street, Ashgrove</p>
</main>
</body>
</html>
```